Lurvik.no is a new website about pedagogical entrepreneurship. It's main target group is teachers. The Nordic Bureau for Digital Schooling and the National Office for Learning and Classrooms are leading the project.

The web page is meant to show examples of how different methods of entrepreneurship can be used pedagogical in a learning environment. The page will also support the user with examples of different teaching programs and other examples of best practice.

Pedagogical entrepreneurship is not about business and men in suits. It's a method for learning. The focus in the design should be on school, education and new ways of learning.

The final product should be motivating and engaging, but at the same time governmental and serious. We are not looking for something "flashy" and corporate-looking, but a moderate, task-focused and clean design that state quality.

We need designs for three pages:
1 - frontpage
2 - subpage ("Metoder og undervisningsopplegg")
3 - subpage ("Små-TOPP i Vassbygd")

The interaction design for these three pages will be uploaded as an attachment.

We would like you to find inspiration in the following websites:
- www.skapekraft.no
- www.giellu.no
- www.brightfernlab.com
- www.zyx.no
(more will be added)

Please use the attached logo, and feel free to use this as an inspiration for the rest of the design.

Target Market(s)

Teachers

Industry/Entity Type

Education

Requirements
Must have
• * Header with: Logo. Main navigation. Utility navigation. Search box.
* Footer
Should not have
• Images of men in suits.
Very strong graphical elements that stands out too much (we want it clean).

```html
<!DOCTYPE html>
<html lang="en">
<head>
<meta charset="utf-8">
<title>Lurvik.no – Pedagogical Entrepreneurship</title>
<link rel="stylesheet" href="https://fonts.googleapis.com/css2?family=Open+Sans:wght@400;600;700&display=swap">
<style>
:root{
  --blue-deep:#0b3f72;
  --blue-mid:#165f9c;
  --blue-light:#2a78b8;
  --blue-text:#1a6aa6;
  --footer:#0f4a82;
  --footer-base:#0a375f;
  --ink:#555;
  --ink-dark:#333;
  --line:#dcdcdc;
  --white:#fff;
  --btn:#1d6aa5;
  --photo-a:#6f8aa0;
}
*{box-sizing:border-box;margin:0;padding:0}
html,body{width:771px;height:1200px;overflow:hidden}
body{font-family:"Open Sans",Arial,sans-serif;background:var(--white);position:relative;color:var(--ink)}
.abs{position:absolute}
a{color:inherit;text-decoration:none}
h1,h2,h3,h4{font-weight:400}

.topstrip{left:0;top:0;width:771px;height:5px;background:#e6e6e6}
.hero{left:0;top:5px;width:771px;height:365px;background:linear-gradient(180deg,var(--blue-deep) 0%,var(--blue-mid) 55%,var(--blue-light) 100%)}

.search{left:626px;top:18px;width:110px;height:14px;border-radius:7px;background:var(--white);font-size:8px;font-style:italic;color:#555;padding:1px 0 0 7px}
.search svg{position:absolute;right:5px;top:3px}

.brand{left:30px;top:44px;display:flex;align-items:center;gap:18px}
.brand-mark{width:46px;height:46px;border-radius:50%;background:#cfe3f3}
.brand-name{font-size:33px;font-weight:600;color:#9fd0f2;line-height:1;letter-spacing:-1px}
.brand-tag{left:97px;top:82px;font-size:6.5px;color:#cfe3f3;white-space:nowrap}

.mainnav{left:316px;top:61px;display:flex;align-items:center;font-size:10px;color:var(--white);white-space:nowrap}
.mainnav a{padding:0 18px}
.mainnav .sep{width:1px;height:12px;background:#7fb0d8}
.mainnav .active{background:#f3f6f8;color:var(--blue-deep);border-radius:3px;padding:5px 8px;margin-right:11px}
.mainnav a:last-child{padding-right:0}

.hero-title{left:42px;top:148px;font-size:18.5px;color:var(--white)}
.hero-rule{left:42px;top:176px;width:268px;height:1px;background:#4a86bb}
.hero-copy{left:42px;top:181px;width:268px;font-size:8px;line-height:13.6px;color:#e8f1f8}
.hero-copy p+p{margin-top:3px}
.hero-btn{left:41px;top:292px;width:84px;height:18px;border-radius:9px;background:#0e3e66;color:#cfe0ee;font-size:8px;text-align:center;line-height:18px}

.slide{left:352px;top:121px;width:374px;height:206px;border:3px solid #d7dde2;box-shadow:0 4px 10px rgba(0,0,0,.35);background:linear-gradient(160deg,#d8dadb 0%,#b7bcc0 45%,var(--photo-a) 100%)}
.arrow{width:16px;height:20px;background:#0d3a63;border-radius:3px;display:flex;align-items:center;justify-content:center}
.arrow-l{left:336px;top:214px}
.arrow-r{left:728px;top:214px}
.dots{left:529px;top:345px;display:flex;gap:3px}
.dots span{width:6px;height:6px;border-radius:50%;background:var(--white)}

.features{left:0;top:370px;width:771px;height:176px;background:linear-gradient(180deg,#fff 0%,#f3f3f3 100%);border-bottom:1px solid #d0d0d0;box-shadow:0 2px 3px rgba(0,0,0,.12);display:flex}
.feature{height:100%;position:relative;border-right:1px solid var(--line)}
.feature-a{width:268px}
.feature-b{width:248px}
.feature-c{width:255px;border-right:0}
.feature-icon{position:absolute}
.feature h2{position:absolute;font-size:13.5px;color:var(--ink-dark);line-height:17px;white-space:nowrap}
.feature p{position:absolute;font-size:8px;line-height:13.5px;color:var(--ink)}
.feature .btn{position:absolute;background:var(--btn);color:var(--white);font-size:7.5px;padding:2px 7px}

.welcome-title{left:31px;top:569px;font-size:14px;color:var(--blue-text)}
.welcome-lead{left:32px;top:596px;width:466px;font-size:8px;line-height:13.5px;color:var(--blue-text)}
.welcome-body{left:32px;top:658px;width:466px;font-size:8px;line-height:13.5px;color:#666}
.welcome-body p+p{margin-top:3px}

.started{left:523px;top:562px;width:223px;height:30px;border-radius:6px;background:#f2f4f6;border:1px solid #dde1e4;font-size:14px;color:var(--blue-text);padding:5px 0 0 14px}
.list{top:601px;width:104px}
.list h3{background:#eceef0;font-size:10px;color:var(--blue-text);padding-left:12px;height:14px;line-height:14px}
.list li{list-style:none;font-size:8px;color:#666;height:16.4px;line-height:16.4px;padding-left:12px;white-space:nowrap}
.list-method{left:528px}
.list-plan{left:635px}
.list-plan li{padding-left:10px}
.pill{top:757px;width:88px;height:14px;border-radius:7px;background:#0f4a82;color:var(--white);font-size:7.5px;line-height:14px;padding-left:12px}
.pill svg{position:absolute;right:7px;top:4px}

.divider{left:31px;top:797px;width:720px;height:1px;background:#e2e2e2}
.insp-title{left:31px;top:806px;font-size:14px;color:var(--blue-text)}
.cards{left:32px;top:834px;display:flex;gap:6px}
.card{width:168px;height:135px;background:#f4f4f4;position:relative}
.card-photo{position:absolute;left:10px;top:7px;width:150px;height:102px}
.card p{position:absolute;left:8px;top:118px;font-size:10.5px;color:var(--blue-text);white-space:nowrap}
.chev{top:880px}

.footer{left:0;top:995px;width:771px;height:173px;background:var(--footer)}
.fcol{top:1019px}
.fcol h4{font-size:9.5px;font-weight:600;color:var(--white);margin-bottom:8px;white-space:nowrap}
.fcol li{list-style:none;font-size:8px;color:#e4eef7;height:17.3px;line-height:15px;border-bottom:1px solid #2f6598;white-space:nowrap}
.fcol li:last-child{border-bottom:0}
.social{left:618px;top:1040px;display:flex;gap:2px}
.social span{width:15px;height:15px;border-radius:2px;background:#4b8fd0}
.footer-brand{left:618px;top:1084px;display:flex;align-items:center;gap:8px}
.footer-brand .dot{width:20px;height:20px;border-radius:50%;background:#cfe3f3}
.footer-brand span{font-size:18px;font-weight:600;color:#9fd0f2}
.base{left:0;top:1168px;width:771px;height:32px;background:var(--footer-base);font-size:7.5px;color:#9fb6cc;padding:11px 0 0 21px}
</style>
</head>
<body>
<div class="abs topstrip"></div>

<header class="abs hero" aria-label="Header"></header>
<div class="abs search">search here
  <svg width="9" height="9" viewBox="0 0 9 9"><circle cx="3.5" cy="3.5" r="2.6" fill="none" stroke="#333" stroke-width="1.2"/><line x1="5.5" y1="5.5" x2="8.3" y2="8.3" stroke="#333" stroke-width="1.4"/></svg>
</div>
<div class="abs brand"><div class="brand-mark"></div><div class="brand-name">Lurvik</div></div>
<div class="abs brand-tag">Entreprenørielle metoder i undervisningen</div>

<nav class="abs mainnav">
  <a class="active" href="#">Best Practice Schools</a><span class="sep"></span>
  <a href="#">Lurvikmeter</a><span class="sep"></span>
  <a href="#">About Lurvik No.</a><span class="sep"></span>
  <a href="#">Contact Us</a>
</nav>

<h1 class="abs hero-title">Lurvik Punch Line goes here</h1>
<div class="abs hero-rule"></div>
<div class="abs hero-copy">
  <p>Static website is a simple way to get your message out to the public. Static website are cheaper and also it needs less maintenance too. It's the simplest, cheapest and also the basic thing the search engine picks it up very easily.</p>
  <p>We at Brightwave provide you the best simple websites too with total work done as using all the best designing and all done so that you can achieve the goal of yours through our work done</p>
</div>
<a class="abs hero-btn" href="#">Read More here</a>

<div class="abs slide" role="img" aria-label="Photo of a teacher at a chalkboard with pupils raising their hands"></div>
<div class="abs arrow arrow-l"><svg width="6" height="9" viewBox="0 0 6 9"><path d="M5 1 1.5 4.5 5 8" fill="none" stroke="#fff" stroke-width="1.5"/></svg></div>
<div class="abs arrow arrow-r"><svg width="6" height="9" viewBox="0 0 6 9"><path d="M1 1 4.5 4.5 1 8" fill="none" stroke="#fff" stroke-width="1.5"/></svg></div>
<div class="abs dots"><span></span><span></span><span></span><span></span></div>

<section class="abs features">
  <div class="feature feature-a">
    <svg class="feature-icon" style="left:45px;top:19px" width="20" height="20" viewBox="0 0 20 20"><circle cx="10" cy="10" r="9" fill="#d6e7f5" stroke="#8fb9dc"/><circle cx="10" cy="10" r="4.5" fill="#1f78c4"/></svg>
    <h2 style="left:73px;top:19px">What is pedagogical<br>entrepreneurship</h2>
    <p style="left:42px;top:61px;width:212px">To be the best we know what and how to present beautifully the working of the client's need and their advantages be highlighted. We act in accordance with the Industry certified processes to deliver the best to our clients all over the world.</p>
    <a class="btn" style="left:41px;top:136px" href="#">read more</a>
  </div>
  <div class="feature feature-b">
    <svg class="feature-icon" style="left:24px;top:18px" width="20" height="22" viewBox="0 0 20 22"><path d="M10 1 19 4v7c0 5-4 9-9 10C5 20 1 16 1 11V4Z" fill="#3aa33a"/><path d="M5.5 11 9 14.5 15 7.5" fill="none" stroke="#fff" stroke-width="2.2"/></svg>
    <h2 style="left:48px;top:20px">Methods and Teaching Plans</h2>
    <p style="left:25px;top:45px;width:210px">To be the best we know what and how to present beautifully the working of the client's need and their advantages be highlighted.<span style="display:block;height:4px"></span>We act in accordance with the Industry certified processes to deliver the best to our clients all over the world.</p>
    <a class="btn" style="left:25px;top:139px" href="#">read more</a>
  </div>
  <div class="feature feature-c">
    <svg class="feature-icon" style="left:24px;top:20px" width="20" height="20" viewBox="0 0 20 20"><rect x="1" y="1" width="18" height="18" rx="4" fill="#e8a070"/></svg>
    <h2 style="left:55px;top:17px">Good examples/<br>best practice</h2>
    <p style="left:19px;top:57px;width:212px">To be the best we know what and how to present beautifully the working of the client's need and their advantages be highlighted. We act in accordance with the Industry certified processes to deliver the best to our clients all over the world.</p>
    <a class="btn" style="left:19px;top:135px" href="#">read more</a>
  </div>
</section>

<h2 class="abs welcome-title">Welcome to Our Website Mainpage</h2>
<p class="abs welcome-lead">Brightwave eStudio is a professional website design company dedicated to provide excellent services. We at Brightwave eStudio think graphic design as a combination and collaboration of ideas and technology. Our Website Design team give an unforgettable impression on the customers and the clients. We can assure you that this is the best place for requirement of yours regarding website design solutions</p>
<div class="abs welcome-body">
  <p>E-Commerce is a major progress in technology that has changed the way in which the customers now purchase information, products and the services. It's the new way of providing an opportunity to make your products and services available in the global market 24 hours a day through Internet</p>
  <p>Brightwave eStudio is specialized in handling advanced web projects and the ongoing projects that require permanent maintenance and support .We like challenges and do complete these challenge with expertise we like solving questions that arises in such projects as these helps us to grow also. When considering advanced web development project, finding the right answers to the hard questions is a challenge for any firm, it includes expertise and enables Brightwave eStudio to specialize in advanced projects and ongoing projects that require permanent support and maintenance.</p>
</div>

<div class="abs started">Get Started Now</div>
<div class="abs list list-method">
  <h3>Method</h3>
  <ul><li>Cafe-Pedagogikk</li><li>Elevbedrift</li><li>Grundercamp</li><li>Story Line</li><li>REAL</li><li>Cafe-Pedagogikk</li><li>Elevbedrift</li><li>Grundercamp</li></ul>
</div>
<div class="abs list list-plan">
  <h3>Teaching Plan</h3>
  <ul><li>Your Teaching Plan here</li><li>Teaching Plan here</li><li>Your Teaching Plan here</li><li>Teaching Plan here</li><li>Your Teaching Plan here</li><li>Teaching Plan here</li><li>Plan here</li><li>Teaching Plan here</li></ul>
</div>
<a class="abs pill" style="left:538px" href="#">See More Here<svg width="4" height="6" viewBox="0 0 4 6"><path d="M0 0 4 3 0 6Z" fill="#fff"/></svg></a>
<a class="abs pill" style="left:643px" href="#">See More Here<svg width="4" height="6" viewBox="0 0 4 6"><path d="M0 0 4 3 0 6Z" fill="#fff"/></svg></a>

<div class="abs divider"></div>
<h2 class="abs insp-title">Inspirations</h2>
<svg class="abs chev" style="left:14px" width="12" height="26" viewBox="0 0 12 26"><path d="M10 1 2 13l8 12" fill="none" stroke="#ccc" stroke-width="2"/></svg>
<svg class="abs chev" style="left:728px" width="12" height="26" viewBox="0 0 12 26"><path d="M2 1l8 12-8 12" fill="none" stroke="#ccc" stroke-width="2"/></svg>
<div class="abs cards">
  <div class="card"><div class="card-photo" role="img" aria-label="Photo of a teacher reading with young pupils" style="background:linear-gradient(135deg,#b98a7a,#6f5e58)"></div><p>Små-TOPP at Vassbygd School</p></div>
  <div class="card"><div class="card-photo" role="img" aria-label="Photo of a teacher helping a pupil at a desk" style="background:linear-gradient(135deg,#9fb8cc,#c9a58d)"></div><p>Små-TOPP at Vassbygd School</p></div>
  <div class="card"><div class="card-photo" role="img" aria-label="Photo of a classroom presentation on a projector screen" style="background:linear-gradient(135deg,#3b4f8a,#8b6a55)"></div><p>Små-TOPP at Vassbygd School</p></div>
  <div class="card"><div class="card-photo" role="img" aria-label="Photo of a teacher in front of pupils at a board" style="background:linear-gradient(135deg,#7d9a8a,#a88672)"></div><p>Små-TOPP at Vassbygd School</p></div>
</div>

<footer class="abs footer"></footer>
<div class="abs fcol" style="left:31px;width:145px"><h4>Pedagogical Entrepreneurship</h4><ul><li>What is Pedagogical Entrenership?</li><li>Science</li><li>Best Practice Schools</li><li>Lurvikmetret</li><li>About Us</li></ul></div>
<div class="abs fcol" style="left:204px;width:112px"><h4>Teaching Plan</h4><ul><li>Teaching plan here</li><li>Teaching plan here</li><li>Teaching plan here</li><li>Teaching plan here</li><li>Teaching plan here</li></ul></div>
<div class="abs fcol" style="left:339px;width:96px"><h4>Methods</h4><ul><li>Storyline</li><li>REAL</li><li>CafePedahgogikk</li><li>More here</li><li>More here</li></ul></div>
<div class="abs fcol" style="left:461px;width:128px"><h4>Gode Eksempler</h4><ul><li>Små-TOPP at Vassbygd Schools</li><li>Små-TOPP at Vassbygd Schools</li><li>Små-TOPP at Vassbygd Schools</li><li>Små-TOPP at Vassbygd Schools</li><li>Små-TOPP at Vassbygd Schools</li></ul></div>
<div class="abs fcol" style="left:617px"><h4>Connect With Us</h4></div>
<div class="abs social"><span></span><span></span><span></span><span></span></div>
<div class="abs footer-brand"><div class="dot"></div><span>Lurvik</span></div>
<div class="abs base">copyright © 2012 Company Name &nbsp;|&nbsp; All right reserved</div>
</body>
</html>
```